Corporate Business Card

Very professional, Modern, Not to busy, include phone address email, website
(253) 617-4930, 18761 52nd Avenue S, Kent, WA 98047, martin@plumlinegroup.com, varkoworks.com

Target Market(s)

Manufacturing

Industry/Entity Type

Aero, machining, manufacturing, Off road racing

Contact Information for Business Card

Phone, address email, website

```html
<!DOCTYPE html>
<html lang="en">
<head>
<meta charset="utf-8">
<title>Varko Works – Business Card</title>
<link rel="stylesheet" href="https://fonts.googleapis.com/css2?family=Montserrat:wght@500;700&display=swap">
<style>
  :root {
    --navy: #163468;
    --red: #d4232b;
    --white: #ffffff;
    --ink: #1a1a1a;
    --backdrop: #3b3b3b;
  }
  * { margin: 0; padding: 0; box-sizing: border-box; }
  html, body {
    width: 1200px; height: 904px; overflow: hidden;
    background: var(--backdrop);
    font-family: "Montserrat", Arial, sans-serif;
  }
  .stage {
    width: 1200px; height: 904px;
    display: flex; flex-direction: column; align-items: center; justify-content: center;
    gap: 40px;
  }
  .card {
    position: relative;
    width: 700px; height: 400px;
    overflow: hidden;
    box-shadow: 0 8px 22px rgba(0,0,0,0.45);
  }
  .card--front { background: var(--navy); }
  .card--back { background: var(--white); }

  .brand {
    position: absolute;
    display: flex; flex-direction: column; align-items: flex-start;
  }
  .brand__row { display: flex; align-items: center; gap: 12px; }
  .brand__square { width: 22px; height: 22px; background: var(--red); flex: none; }
  .brand__name { font-weight: 700; letter-spacing: 1px; white-space: nowrap; line-height: 1; }
  .brand__rule { height: 2px; margin-top: 24px; }

  .card--front .brand { left: 120px; top: 140px; }
  .card--front .brand__name { color: var(--white); font-size: 52px; }
  .card--front .brand__rule { width: 240px; background: var(--white); }

  .card--back .brand { right: 44px; top: 60px; }
  .card--back .brand__square { width: 18px; height: 18px; }
  .card--back .brand__name { color: var(--navy); font-size: 36px; }
  .card--back .brand__rule { width: 180px; margin-top: 20px; background: var(--navy); }

  .address {
    position: absolute; left: 58px; top: 146px;
    color: var(--ink); font-weight: 500; font-size: 15px; line-height: 1.45;
  }
  .contacts {
    position: absolute; left: 58px; top: 206px;
    list-style: none; color: var(--ink); font-weight: 500; font-size: 15px;
  }
  .contacts li { display: flex; align-items: center; gap: 10px; height: 24px; }
  .contacts svg { width: 16px; height: 16px; flex: none; }
  .wave { position: absolute; left: 0; top: 0; width: 700px; height: 400px; }
</style>
</head>
<body>
<main class="stage">
  <section class="card card--front" aria-label="Card front">
    <div class="brand">
      <div class="brand__row">
        <span class="brand__square"></span>
        <span class="brand__name">VARKO WORKS</span>
      </div>
      <div class="brand__rule"></div>
    </div>
  </section>

  <section class="card card--back" aria-label="Card back">
    <svg class="wave" viewBox="0 0 700 400" aria-hidden="true">
      <path d="M0,355 C140,305 260,312 400,288 C530,262 640,215 700,160 L700,400 L0,400 Z" fill="var(--navy)"/>
      <path d="M0,355 C140,305 260,312 400,288 C530,262 640,215 700,160" fill="none" stroke="var(--red)" stroke-width="4"/>
    </svg>

    <div class="brand">
      <div class="brand__row">
        <span class="brand__square"></span>
        <span class="brand__name">VARKO WORKS</span>
      </div>
      <div class="brand__rule"></div>
    </div>

    <p class="address">18761 52nd Avenue<br>S, Kent, WA 98047</p>

    <ul class="contacts">
      <li>
        <svg viewBox="0 0 16 16" aria-hidden="true"><path fill="var(--red)" d="M3.5 1.5l2.3 2.8-1.3 1.8c.9 2 2.4 3.5 4.4 4.4l1.8-1.3 2.8 2.3-1.4 2.2C6.6 13.4 2.6 9.4 1.3 3.3z"/></svg>
        <span>(253) 617-4930</span>
      </li>
      <li>
        <svg viewBox="0 0 16 16" aria-hidden="true"><rect x="1" y="3.5" width="14" height="9" fill="var(--red)"/><path d="M1.5 4l6.5 5 6.5-5" fill="none" stroke="var(--white)" stroke-width="1.2"/></svg>
        <span>martin@plumlinegroup.com</span>
      </li>
      <li>
        <svg viewBox="0 0 16 16" aria-hidden="true"><circle cx="8" cy="8" r="7" fill="var(--red)"/><path d="M1 8h14M8 1c-3 3.5-3 10.5 0 14M8 1c3 3.5 3 10.5 0 14" fill="none" stroke="var(--white)" stroke-width="1"/></svg>
        <span>www.varkoworks.com</span>
      </li>
    </ul>
  </section>
</main>
</body>
</html>
```